Business Card Design For Marketing Agnecy LVP

Need business card design for marketing agency.

Doug Fenwick
President, CEO
1-555-302-4196
doug@boldpromoperksgroup.example
www.BoldPromoPerksGroup.example

Back Side:
Boost Sales Using Rewards, Incentives & Giveaways
Get A Free Sample Package

Target Market(s)

B2B

Industry/Entity Type

Marketing

Contact Information for Business Card

Doug Fenwick
President, CEO
1-555-302-4196

Back Side:
Get A Free Sample Package

Please note that my current url is OLD DESIGN. I am working on new design and want the business card to match color themes at least on new site. Here is the demo link for new site so you can see the colors I use, etc.

http://layoutcratehub.example/kq/doug/lvp_final/index.html

Requirements
Must have
• Please note that my current url is OLD DESIGN. I am working on new design and want the business card to match color themes at least on new site. Here is the demo link for new site so you can see the colors I use, etc.

Nice to have

Should not have

```html
<!DOCTYPE html>
<html lang="en">
<head>
<meta charset="utf-8">
<title>LVP Business Card</title>
<link rel="stylesheet" href="https://fonts.googleapis.com/css2?family=Montserrat:wght@600;700&family=Arimo:wght@400&display=swap">
<style>
  :root {
    --backdrop: #2b2b2d;
    --card: #0e0e10;
    --card-edge: #161618;
    --brand-blue: #1f78c8;
    --text-grey: #b9b9bb;
    --rule-grey: #55565a;
    --glyph-dark: #0e0e10;
  }
  * { margin: 0; padding: 0; box-sizing: border-box; }
  html, body {
    width: 1200px;
    height: 900px;
    overflow: hidden;
    background: var(--backdrop);
  }
  .canvas {
    position: relative;
    width: 1200px;
    height: 900px;
  }
  .card {
    position: absolute;
    left: 320px;
    width: 560px;
    height: 320px;
    background: linear-gradient(160deg, var(--card-edge), var(--card) 60%);
    overflow: hidden;
  }
  .card::after {
    content: "";
    position: absolute;
    left: 0; right: 0; bottom: 0;
    height: 10px;
    background: var(--brand-blue);
  }
  .card--front { top: 110px; }
  .card--back { top: 470px; }

  .brand-name {
    position: absolute;
    top: 50%;
    left: 50%;
    transform: translate(-50%, -58%);
    font-family: "Arimo", sans-serif;
    font-weight: 400;
    font-size: 48px;
    letter-spacing: 6px;
    color: var(--text-grey);
    line-height: 1;
    white-space: nowrap;
  }

  .contact {
    position: absolute;
    top: 40px;
    left: 0; right: 0;
    text-align: center;
    font-family: "Arimo", sans-serif;
    color: var(--text-grey);
  }
  .contact__name {
    font-family: "Montserrat", sans-serif;
    font-weight: 700;
    font-size: 19px;
    letter-spacing: 0.5px;
    text-transform: uppercase;
    color: var(--brand-blue);
  }
  .contact__title {
    font-size: 15px;
    margin-top: 2px;
  }
  .contact__icons {
    display: flex;
    align-items: center;
    justify-content: center;
    gap: 6px;
    margin: 8px auto 6px;
    width: 170px;
  }
  .contact__icons .rule {
    flex: 1;
    height: 1px;
    background: var(--rule-grey);
  }
  .contact__icons svg { display: block; }
  .contact__line {
    font-size: 15px;
    line-height: 1.3;
  }
  .contact__divider {
    width: 170px;
    height: 1px;
    background: var(--rule-grey);
    margin: 10px auto 12px;
  }
  .contact__tagline {
    font-size: 15px;
    line-height: 1.35;
  }
  .contact__tagline .bullet {
    display: inline-block;
    width: 7px;
    height: 7px;
    border-radius: 50%;
    background: var(--text-grey);
    margin: 0 6px;
    vertical-align: middle;
  }
</style>
</head>
<body>
<main class="canvas">
  <section class="card card--front" aria-label="Card front">
    <span class="brand-name">LVP</span>
  </section>

  <section class="card card--back" aria-label="Card back">
    <div class="contact">
      <h1 class="contact__name">Doug Fenwick</h1>
      <p class="contact__title">President, CEO</p>
      <div class="contact__icons">
        <span class="rule"></span>
        <svg width="18" height="18" viewBox="0 0 18 18" aria-label="Phone">
          <rect width="18" height="18" rx="3" fill="var(--brand-blue)"/>
          <path d="M5 6.5c0-1 .6-1.5 1.2-1.5h5.6c.6 0 1.2.5 1.2 1.5v.8h-2V6.5H7v.8H5z" fill="var(--glyph-dark)"/>
          <rect x="5" y="8.5" width="8" height="4.5" rx="1" fill="var(--glyph-dark)"/>
        </svg>
        <svg width="18" height="18" viewBox="0 0 18 18" aria-label="Email">
          <rect width="18" height="18" rx="3" fill="var(--brand-blue)"/>
          <rect x="4" y="5.5" width="10" height="7" fill="var(--glyph-dark)"/>
          <path d="M4.5 6l4.5 3.6L13.5 6" stroke="var(--brand-blue)" stroke-width="1.1" fill="none"/>
        </svg>
        <svg width="18" height="18" viewBox="0 0 18 18" aria-label="Website">
          <rect width="18" height="18" rx="3" fill="var(--brand-blue)"/>
          <circle cx="9" cy="9" r="4.8" fill="var(--glyph-dark)"/>
          <path d="M4.4 9h9.2M9 4.3c-1.6 2.6-1.6 6.8 0 9.4M9 4.3c1.6 2.6 1.6 6.8 0 9.4" stroke="var(--brand-blue)" stroke-width="0.9" fill="none"/>
        </svg>
        <span class="rule"></span>
      </div>
      <p class="contact__line">1-555-302-4196</p>
      <p class="contact__line">doug@boldpromoperksgroup.example</p>
      <p class="contact__line">www.BoldPromoPerksGroup.example</p>
      <div class="contact__divider"></div>
      <p class="contact__tagline">Boost Sales Using Rewards<span class="bullet"></span>Incentives &amp; Giveaways</p>
      <p class="contact__tagline">Get A Free Sample Package</p>
    </div>
  </section>
</main>
</body>
</html>
```